TALMORK

The business want a professional looking business card. We have a scetch we will add but want the extra upgrade, and would like more suggestions for variations of our business cards.

```html
<!DOCTYPE html>
<html lang="en">
<head>
<meta charset="utf-8">
<title>Talmork – Business Card Variations</title>
<link rel="stylesheet" href="https://fonts.googleapis.com/css2?family=Cinzel:wght@500;600&family=Jost:wght@400;500&display=swap">
<style>
  :root{
    --backdrop:#e6ddd1;
    --cream:#f1ece3;
    --ink:#1a1612;
    --black:#161514;
    --forest:#1e2c21;
    --gold:#b8893a;
    --gold-light:#d7b066;
    --gold-card-a:#c59c4f;
    --gold-card-b:#e2c584;
    --brown:#3c2c12;
    --muted:#2e2a25;
  }
  *{margin:0;padding:0;box-sizing:border-box}
  html,body{width:1200px;height:704px;overflow:hidden;background:var(--backdrop)}
  body{position:relative;font-family:"Jost",sans-serif}
  .sheet{position:absolute;inset:0}
  .card{position:absolute;width:364px;height:216px;border-radius:9px;overflow:hidden;color:var(--muted)}
  .card--cream{background:var(--cream)}
  .card--black{background:var(--black);color:#e9e2d4}
  .card--gold{background:linear-gradient(115deg,var(--gold-card-a),var(--gold-card-b) 55%,var(--gold-card-a));color:var(--brown)}
  .card--forest{background:var(--forest);color:#e9e2d4}
  .col-1{left:33px}.col-2{left:415px}.col-3{left:797px}
  .row-1{top:15px}.row-2{top:247px}.row-3{top:479px}

  .wordmark{position:absolute;font-family:"Cinzel",serif;font-weight:500;font-size:27px;letter-spacing:3px;line-height:1;color:var(--brown)}
  .card--black .wordmark,.card--forest .wordmark{color:var(--gold-light)}
  .card--cream .wordmark{color:#3a2c18}
  .subtitle{position:absolute;font-family:"Jost",sans-serif;font-weight:500;font-size:13px;letter-spacing:4.5px;line-height:1;color:inherit}
  .card--black .subtitle,.card--forest .subtitle{color:var(--gold-light)}
  .role{position:absolute;font-size:14px;line-height:1.2}
  .person{position:absolute;font-size:11px;line-height:1.2}
  .card--black .role,.card--black .person,.card--forest .role,.card--forest .person{color:var(--gold-light)}
  .contacts{position:absolute;list-style:none;font-size:10.8px}
  .contacts li{display:flex;align-items:center;gap:12px;height:20px}
  .card--black .contacts,.card--forest .contacts{color:#f0e9dc}
  .icon{width:11px;height:11px;fill:none;stroke:currentColor;stroke-width:1.4}
  .since{position:absolute;font-size:8.5px;letter-spacing:2.6px;line-height:1}
  .card--black .since,.card--forest .since{color:var(--gold-light)}
  .rule{position:absolute;width:1px;background:currentColor;opacity:.45}
  .card--cream .rule{background:var(--gold)}
  .mark{position:absolute;display:flex;align-items:center;gap:6px;font-family:"Cinzel",serif;font-weight:600;font-size:13px;letter-spacing:2px;color:var(--gold)}
  .mark::before{content:"";width:10px;height:10px;border-radius:50%;background:currentColor}
  .card--gold .mark{color:var(--brown)}
  .card--black .mark,.card--forest .mark{color:var(--gold-light)}
  .center{left:0;right:0;text-align:center}
  .band{position:absolute;left:0;right:0;bottom:0;height:64px;background:linear-gradient(115deg,var(--gold-card-a),var(--gold-card-b) 55%,var(--gold-card-a));color:var(--brown);display:flex;justify-content:space-between;padding:14px 26px 0 26px;font-size:10px}
  .band .item{display:flex;flex-direction:column;align-items:center;gap:9px}
</style>
</head>
<body>
<svg width="0" height="0" style="position:absolute" aria-hidden="true">
  <symbol id="i-phone" viewBox="0 0 12 12"><rect x="3" y="0.8" width="6" height="10.4" rx="1.2"/><line x1="5.2" y1="9.3" x2="6.8" y2="9.3"/></symbol>
  <symbol id="i-mail" viewBox="0 0 12 12"><rect x="0.8" y="2.3" width="10.4" height="7.4"/><polyline points="0.8,2.3 6,6.6 11.2,2.3"/></symbol>
  <symbol id="i-web" viewBox="0 0 12 12"><circle cx="6" cy="6" r="5"/><ellipse cx="6" cy="6" rx="2.2" ry="5"/><line x1="1" y1="6" x2="11" y2="6"/></symbol>
</svg>

<main class="sheet">
  <!-- Row 1 -->
  <section class="card card--cream col-1 row-1">
    <div class="wordmark" style="left:27px;top:38px">TALMORK</div>
    <div class="subtitle" style="left:28px;top:72px">BRENNHAUG</div>
    <div class="role" style="left:28px;top:104px">CEO &amp; Founder</div>
    <div class="person" style="left:28px;top:122px">Aksel Viktor Brennhaug</div>
    <ul class="contacts" style="left:26px;top:150px">
      <li><svg class="icon"><use href="#i-phone"/></svg>004791234567</li>
      <li><svg class="icon"><use href="#i-mail"/></svg>talmork.llc@postline.com</li>
      <li><svg class="icon"><use href="#i-web"/></svg>www.talmork.llc</li>
    </ul>
    <div class="mark" style="left:230px;top:96px">TALMORK</div>
    <div class="since" style="left:252px;top:202px;top:198px">SINCE 2026</div>
  </section>

  <section class="card card--black col-2 row-1">
    <div class="wordmark" style="left:27px;top:38px">TALMORK</div>
    <div class="subtitle" style="left:28px;top:72px">BRENNHAUG</div>
    <div class="role" style="left:28px;top:104px">CEO &amp; Founder</div>
    <div class="person" style="left:28px;top:122px">Aksel Viktor Brennhaug</div>
    <ul class="contacts" style="left:26px;top:150px">
      <li><svg class="icon"><use href="#i-phone"/></svg>004791234567</li>
      <li><svg class="icon"><use href="#i-mail"/></svg>talmork.llc@postline.com</li>
      <li><svg class="icon"><use href="#i-web"/></svg>www.talmork.llc</li>
    </ul>
    <div class="since" style="left:263px;top:200px">SINCE 2026</div>
  </section>

  <section class="card card--gold col-3 row-1">
    <div class="wordmark" style="left:28px;top:38px">TALMORK</div>
    <div class="subtitle" style="left:29px;top:72px">BRENNHAUG</div>
    <div class="role" style="left:29px;top:104px">CEO &amp; Founder</div>
    <div class="person" style="left:29px;top:122px">Aksel Viktor Brennhaug</div>
    <ul class="contacts" style="left:27px;top:150px">
      <li><svg class="icon"><use href="#i-phone"/></svg>004791234567</li>
      <li><svg class="icon"><use href="#i-mail"/></svg>talmork.llc@postline.com</li>
      <li><svg class="icon"><use href="#i-web"/></svg>www.talmork.llc</li>
    </ul>
    <div class="rule" style="left:232px;top:52px;height:126px"></div>
    <div class="mark" style="left:254px;top:108px">TALMORK</div>
    <div class="since" style="left:267px;top:172px">SINCE 2026</div>
  </section>

  <!-- Row 2 -->
  <section class="card card--gold col-1 row-2">
    <div class="wordmark" style="left:27px;top:34px;font-size:18px;letter-spacing:1px">TALMORK BRENNHAUG</div>
    <div class="role" style="left:28px;top:61px">CEO &amp; Founder</div>
    <div class="person" style="left:28px;top:80px">Aksel Viktor Brennhaug</div>
    <ul class="contacts" style="left:27px;top:136px">
      <li><svg class="icon"><use href="#i-phone"/></svg>004791234567</li>
      <li><svg class="icon"><use href="#i-mail"/></svg>talmork.llc@postline.com</li>
      <li><svg class="icon"><use href="#i-web"/></svg>www.talmork.llc</li>
    </ul>
    <div class="rule" style="left:208px;top:70px;height:104px"></div>
    <div class="mark" style="left:234px;top:150px">TALMORK</div>
    <div class="since" style="left:247px;top:172px;font-size:7.5px">SINCE 2026</div>
  </section>

  <section class="card card--cream col-2 row-2">
    <div class="wordmark" style="left:28px;top:32px">TALMORK</div>
    <div class="subtitle" style="left:29px;top:64px">BRENNHAUG</div>
    <div class="role" style="left:29px;top:92px">CEO &amp; Founder</div>
    <div class="person" style="left:29px;top:109px">Aksel Viktor Brennhaug</div>
    <ul class="contacts" style="left:27px;top:136px">
      <li><svg class="icon"><use href="#i-phone"/></svg>004791234567</li>
      <li><svg class="icon"><use href="#i-mail"/></svg>talmork.llc@postline.com</li>
      <li><svg class="icon"><use href="#i-web"/></svg>www.talmork.llc</li>
    </ul>
    <div class="mark" style="left:250px;top:144px">TALMORK</div>
    <div class="since" style="left:270px;top:195px">SINCE 2026</div>
  </section>

  <section class="card card--forest col-3 row-2">
    <div class="mark" style="left:140px;top:26px">TALMORK</div>
    <div class="wordmark center" style="top:70px;font-size:22px;letter-spacing:4px">TALMORK</div>
    <div class="subtitle center" style="top:96px;font-size:11px">BRENNHAUG</div>
    <div class="role center" style="top:118px;font-size:11px">CEO &amp; Founder</div>
    <div class="person center" style="top:133px;font-size:11px">Aksel Viktor Brennhaug</div>
    <ul class="contacts" style="left:17px;top:146px">
      <li><svg class="icon"><use href="#i-phone"/></svg>004791234567</li>
      <li><svg class="icon"><use href="#i-mail"/></svg>talmork.llc@postline.com</li>
      <li><svg class="icon"><use href="#i-web"/></svg>www.talmork.llc</li>
    </ul>
    <div class="since" style="left:282px;top:186px">SINCE 2026</div>
  </section>

  <!-- Row 3 -->
  <section class="card card--cream col-1 row-3">
    <div class="mark" style="left:28px;top:78px">TALMORK</div>
    <div class="since" style="left:30px;top:156px">SINCE 2026</div>
    <div class="rule" style="left:124px;top:22px;height:182px"></div>
    <div class="wordmark" style="left:153px;top:32px">TALMORK</div>
    <div class="subtitle" style="left:154px;top:62px">BRENNHAUG</div>
    <div class="role" style="left:154px;top:86px;font-size:12.5px">CEO &amp; Founder</div>
    <div class="person" style="left:154px;top:103px">Aksel Viktor Brennhaug</div>
    <ul class="contacts" style="left:153px;top:128px">
      <li><svg class="icon"><use href="#i-phone"/></svg>004791234567</li>
      <li><svg class="icon"><use href="#i-mail"/></svg>talmork.llc@postline.com</li>
      <li><svg class="icon"><use href="#i-web"/></svg>www.talmork.llc</li>
    </ul>
  </section>

  <section class="card card--black col-2 row-3">
    <div class="wordmark center" style="top:50px;font-size:31px;letter-spacing:5px">TALMORK</div>
    <div class="since center" style="top:96px;font-size:10.5px;letter-spacing:4px">SINCE 2026</div>
    <div class="band">
      <div class="item"><svg class="icon"><use href="#i-phone"/></svg>004791234567</div>
      <div class="item"><svg class="icon"><use href="#i-mail"/></svg>talmork.llc@postline.com</div>
      <div class="item"><svg class="icon"><use href="#i-web"/></svg>www.talmork.llc</div>
    </div>
  </section>

  <section class="card card--black col-3 row-3">
    <div class="mark" style="left:28px;top:80px">TALMORK</div>
    <div class="since" style="left:28px;top:158px">SINCE 2026</div>
    <div class="rule" style="left:129px;top:30px;height:174px;background:var(--gold-light);opacity:.8"></div>
    <div class="wordmark" style="left:166px;top:30px">TALMORK</div>
    <div class="subtitle" style="left:167px;top:61px">BRENNHAUG</div>
    <div class="role" style="left:167px;top:84px;font-size:12.5px">CEO &amp; Founder</div>
    <div class="person" style="left:167px;top:101px">Aksel Viktor Brennhaug</div>
    <ul class="contacts" style="left:165px;top:128px">
      <li><svg class="icon"><use href="#i-phone"/></svg>004791234567</li>
      <li><svg class="icon"><use href="#i-mail"/></svg>talmork.llc@postline.com</li>
      <li><svg class="icon"><use href="#i-web"/></svg>www.talmork.llc</li>
    </ul>
  </section>
</main>
</body>
</html>
```